real esate business card with company logo and name

we need a business card design for a real esate company

The company name is Walsh & Brand Pty Ltd, and we have our logo designed and will upload. We want classic or moden feel. Black or white background. looks more textured. Should include folowinginformations
Owen Walsh and Lucy Brand
Sales Agents & Onsite Manager
p: 07 5948 2063
F: 07 5948 2174
M:0431 857 219
3/42 Marlow Crescent, FERNLEA QLD 4213

We want this business card looks professonal. Thank you in advance.

Industry/Entity Type

Real Estate Agent

Contact Information for Business Card

Owen Walsh and Lucy Brand
Onsite Manager & Sales Agents
p: 07 5948 2063
M:0431 857 219

Font styles to use
Serif

Colors
000000
fbfbfb
333333
959595

Requirements
Must have
• company logo and name, black or white back ground

```html
<!DOCTYPE html>
<html lang="en">
<head>
<meta charset="utf-8">
<title>Walsh &amp; Brand Pty Ltd — Business Card</title>
<link rel="stylesheet" href="https://fonts.googleapis.com/css2?family=Lato:wght@400;700&display=swap">
<style>
  :root {
    --canvas: #2b2b2b;
    --card: #000000;
    --text: #fbfbfb;
    --text-soft: #e6e6e6;
    --brand: #959595;
    --bar-light: #d4d4d4;
    --bar-dark: #55555a;
    --rule: #d9d9d9;
  }
  * { margin: 0; padding: 0; box-sizing: border-box; }
  html, body {
    width: 1200px;
    height: 1086px;
    overflow: hidden;
    background: var(--canvas);
    font-family: "Lato", Arial, sans-serif;
  }
  .card {
    position: absolute;
    left: 254px;
    width: 677px;
    height: 388px;
    background: var(--card);
    color: var(--text);
  }
  .card--front { top: 126px; }
  .card--back { top: 586px; }

  .brand {
    position: absolute;
    display: flex;
    align-items: center;
    color: var(--brand);
    font-weight: 700;
    letter-spacing: 0.04em;
    text-transform: uppercase;
    white-space: nowrap;
  }
  .brand__mark {
    background: var(--brand);
    flex: none;
  }
  .card--front .brand {
    right: 32px;
    top: 150px;
    font-size: 17px;
    gap: 10px;
  }
  .card--front .brand__mark { width: 22px; height: 22px; }

  .card--back .brand {
    left: 0;
    right: 0;
    top: 176px;
    justify-content: center;
    font-size: 24px;
    gap: 14px;
  }
  .card--back .brand__mark { width: 30px; height: 30px; }

  .agent__name {
    position: absolute;
    left: 32px;
    top: 188px;
    font-size: 28px;
    font-weight: 700;
    line-height: 1;
    color: var(--text-soft);
  }
  .agent__role {
    position: absolute;
    left: 32px;
    top: 224px;
    font-size: 20px;
    line-height: 1;
    color: var(--text-soft);
  }
  .agent__rule {
    position: absolute;
    left: 161px;
    right: 31px;
    top: 237px;
    height: 1.5px;
    background: var(--rule);
  }

  .contact {
    position: absolute;
    left: 32px;
    top: 292px;
    list-style: none;
    font-size: 19px;
    line-height: 23.5px;
    color: var(--text-soft);
  }
  .contact li { display: flex; align-items: center; gap: 6px; }
  .contact svg { width: 16px; height: 16px; fill: var(--text-soft); flex: none; }

  .address {
    position: absolute;
    right: 31px;
    top: 316px;
    text-align: right;
    font-style: normal;
    font-size: 18px;
    line-height: 23px;
    color: var(--text-soft);
  }

  .card__bar {
    position: absolute;
    left: 0;
    right: 0;
    bottom: 0;
    height: 12px;
    display: flex;
  }
  .card__bar-light { width: 535px; background: var(--bar-light); }
  .card__bar-dark { flex: 1; background: var(--bar-dark); }
</style>
</head>
<body>
  <section class="card card--front">
    <div class="brand"><span class="brand__mark"></span>Walsh &amp; Brand Pty Ltd.</div>

    <h1 class="agent__name">Owen Walsh</h1>
    <p class="agent__role">Sales Agents</p>
    <div class="agent__rule"></div>

    <ul class="contact">
      <li>
        <svg viewBox="0 0 16 16" aria-hidden="true"><path d="M4.5 1h7a1 1 0 0 1 1 1v12a1 1 0 0 1-1 1h-7a1 1 0 0 1-1-1V2a1 1 0 0 1 1-1zm.5 2v9h6V3H5zm3 9.8a.8.8 0 1 0 0 .01z"/></svg>
        0431 857 219
      </li>
      <li>
        <svg viewBox="0 0 16 16" aria-hidden="true"><path d="M1 5.5C1 3.5 4 2.5 8 2.5s7 1 7 3v1.5h-3.5V5.2c-1-.3-2.2-.4-3.5-.4s-2.5.1-3.5.4V7H1V5.5zM4 8.5l1.5-2.5h5L12 8.5V14H4V8.5zm4 1a1.7 1.7 0 1 0 0 3.4 1.7 1.7 0 0 0 0-3.4z"/></svg>
        07 5948 2063
      </li>
      <li>
        <svg viewBox="0 0 16 16" aria-hidden="true"><path d="M4 1.5h8v3.5H4zM1.5 6h13v6H12v-2H4v2H1.5zM4.8 11h6.4v3.5H4.8z"/></svg>
        07 5948 2174
      </li>
    </ul>

    <address class="address">
      3/42 Marlow Crescent<br>
      FERNLEA QLD 4213
    </address>

    <div class="card__bar">
      <span class="card__bar-light"></span>
      <span class="card__bar-dark"></span>
    </div>
  </section>

  <section class="card card--back">
    <div class="brand"><span class="brand__mark"></span>Walsh &amp; Brand Pty Ltd.</div>
  </section>
</body>
</html>
```